New Business Card Design for Manufacturing

We are an engineering/manufacturing company that offers Advanced machining/assembly/engineering services, as well as innovative products for the heavy duty engine cooling markets.

We are looking to get a new business card designed that is clean and modern looking, but still fits the wide range of technical/skilled work we do.

- We hope to use this design as the base for other design work in new Presentations, web, and print work.

Industry/Entity Type

Engineering

Contact Information for Business Card

Our preferred color of blue is (RGB) 22/71/159 but can vary slightly from that color. Our content will be our Logo and full company name (Vantrell Forge Works, Inc.), company address, name, job title, phone number with extension, cell number, fax number, website, and email address on the cards.
We'd like the full company name next to the logo, but we are open to other interpretations of that layout.
Preferably, we would like the back side to be clean with just our logo, and the front to contain all of the contact information.

Colors
2f74b4
0355a3
85abd2

Requirements
Must have
• - Logo, company name, needed content - We are open to interpretation beyond that.
• - Standard size business card.
• - Horizontal orientation.
• - Enough space for lengthy names / job titles (for example, a job title could read "Directory of Human Resources" or "V.P. of Governmental Affairs"). We need this to look clean, whether the title be short (CEO) or long (as described above).

```html
<!DOCTYPE html>
<html lang="en">
<head>
<meta charset="utf-8">
<title>Vantrell Forge Works – Business Card</title>
<link href="https://fonts.googleapis.com/css2?family=Roboto:wght@400;700;900&display=swap" rel="stylesheet">
<style>
  :root {
    --brand-blue: #16479f;
    --ink-grey: #555555;
    --rule-grey: #bdbdbd;
    --card-white: #fbfbfb;
    --card-black: #111111;
    --stage: #4a4a4a;
  }
  * { margin: 0; padding: 0; box-sizing: border-box; }
  html, body { width: 1200px; height: 1134px; overflow: hidden; }
  body {
    position: relative;
    background: var(--stage);
    font-family: "Roboto", Arial, sans-serif;
  }
  .card {
    position: absolute;
    left: 261px;
    width: 675px;
    height: 382px;
    overflow: hidden;
  }
  .card--front { top: 161px; background: var(--card-white); }
  .card--back { top: 589px; background: var(--card-black); }

  .brand-name {
    position: absolute;
    left: 39px; top: 44px;
    font-size: 50px; font-weight: 900;
    letter-spacing: 1px;
    color: var(--brand-blue);
    line-height: 1;
  }
  .person { position: absolute; right: 38px; top: 148px; text-align: right; }
  .person__name { font-size: 28px; font-weight: 700; color: var(--brand-blue); line-height: 34px; }
  .person__title { font-size: 18px; color: var(--ink-grey); line-height: 22px; }

  .divider {
    position: absolute; left: 38px; right: 38px; top: 212px;
    height: 2px; background: var(--rule-grey);
  }

  .contacts { position: absolute; left: 40px; top: 230px; list-style: none; }
  .contacts li {
    display: flex; align-items: center; gap: 6px;
    height: 23px; font-size: 16px; color: var(--ink-grey);
  }
  .contacts svg { width: 15px; height: 15px; fill: var(--brand-blue); flex: none; }

  .address { position: absolute; right: 38px; top: 278px; text-align: right; font-size: 16px; line-height: 22px; color: var(--ink-grey); }
  .address__company { color: var(--brand-blue); }

  .footer-band { position: absolute; left: 0; right: 0; bottom: 0; height: 19px; background: var(--card-black); }
  .footer-band__accent {
    position: absolute; top: 0; bottom: 0; left: 436px; right: -20px;
    background: var(--brand-blue);
    transform: skewX(-35deg);
  }

  .back-lockup { position: absolute; left: 139px; top: 164px; display: flex; align-items: center; gap: 26px; }
  .back-lockup__mark { font-size: 50px; font-weight: 900; letter-spacing: 1px; color: #ffffff; line-height: 1; }
  .back-lockup__company { font-size: 19px; font-weight: 900; color: #ffffff; line-height: 20px; text-transform: uppercase; }
</style>
</head>
<body>
  <section class="card card--front" aria-label="Business card front">
    <div class="brand-name">VANTRELL</div>

    <div class="person">
      <div class="person__name">Dana Whitlock</div>
      <div class="person__title">V.P. of Governmental Affairs</div>
    </div>

    <div class="divider"></div>

    <ul class="contacts">
      <li><svg viewBox="0 0 16 16"><path d="M3.5 1l2.5 3-1.5 2c1 2 3 4 5 5l2-1.5 3 2.5-1.5 2.5C8 15 1 8 1 2.5z"/></svg>555 210 4410</li>
      <li><svg viewBox="0 0 16 16"><path d="M4 0h8a1 1 0 0 1 1 1v14a1 1 0 0 1-1 1H4a1 1 0 0 1-1-1V1a1 1 0 0 1 1-1zm1 2v10h6V2zm3 11a1 1 0 1 0 0 2 1 1 0 0 0 0-2z"/></svg>555 210 4482</li>
      <li><svg viewBox="0 0 16 16"><path d="M4 1h8v4H4zM1 6h14v7h-3v2H4v-2H1zm4 5v3h6v-3z"/></svg>555 210 4499</li>
      <li><svg viewBox="0 0 16 16"><path d="M1 3h14v1L8 9 1 4zm0 3l7 5 7-5v7H1z"/></svg>info@vantrellforge.com</li>
      <li><svg viewBox="0 0 16 16"><path d="M8 1a7 7 0 1 0 0 14A7 7 0 0 0 8 1zm0 1.5c.8 0 1.7 1.8 2 4H6c.3-2.2 1.2-4 2-4zM2.6 7.5h2.4c0 1 .1 1.9.3 2.7H3.3a5.5 5.5 0 0 1-.7-2.7zm8.4 0h2.4c0 1-.3 1.9-.7 2.7h-2c.2-.8.3-1.7.3-2.7zM6 7.5h4c0 1-.1 1.9-.3 2.7H6.3C6.1 9.4 6 8.5 6 7.5zm.5 4.2h3c-.4 1.1-1 1.8-1.5 1.8s-1.1-.7-1.5-1.8z"/></svg>www.vantrellforge.com</li>
    </ul>

    <div class="address">
      <div class="address__company">Vantrell Forge Works, Inc.</div>
      <div>Level 2, 17 Harlow Lane</div>
      <div>Ballarat, VIC 3350</div>
    </div>

    <div class="footer-band"><div class="footer-band__accent"></div></div>
  </section>

  <section class="card card--back" aria-label="Business card back">
    <div class="back-lockup">
      <div class="back-lockup__mark">VANTRELL</div>
      <div class="back-lockup__company">Vantrell<br>Forge Works<br>Inc.</div>
    </div>
  </section>
</body>
</html>
```